We Buy Houses Postcard Design

Harborline Asset Partners is one of Baltimore‘s top real estate investing groups because we treat buyers and sellers like real people; not like numbers on a spreadsheet. We specialize in buying distressed properties including multi-family, commercial, retail, single family, and bank REO’s from sellers who need to sell fast. Our website is www.harborlineassetpartners.com. Our phone number is (555) 274-1916. Both need to be on the card. Front and back sides are to be printed. Front full color, back black and white. We want our logo on the design somewhere. The logo can be found on the website. If you need the original files ask me for them. See attached as examples. Return address should be 587 W Tessaly Ave, Suite 319, Baltimore, MD 21209. My name is Marcus. Address label is 1" x 2-5/8". Please leave room for it and postage on the back side.

Industry/Entity Type

Real Estate

```html
<!DOCTYPE html>
<html lang="en">
<head>
<meta charset="utf-8">
<title>Harborline Asset Partners – We Buy Houses Postcard</title>
<link rel="stylesheet" href="https://fonts.googleapis.com/css2?family=Arimo:wght@400;700&display=swap">
<style>
  :root {
    --paper: #ffffff;
    --ink: #1a1a1a;
    --brand-navy: #2e3192;
    --alert-red: #ee1c25;
    --highlight: #fff200;
    --signature-tone: #e9e9e9;
  }
  * { margin: 0; padding: 0; box-sizing: border-box; }
  html, body { width: 1200px; height: 863px; overflow: hidden; background: var(--paper); }
  .postcard {
    position: relative;
    width: 1200px;
    height: 863px;
    background: var(--paper);
    font-family: "Arimo", Arial, sans-serif;
    color: var(--ink);
  }
  .brand-name {
    position: absolute;
    left: 68px;
    top: 88px;
    width: 360px;
    font-size: 38px;
    line-height: 42px;
    font-weight: 400;
    color: var(--brand-navy);
  }
  .copy-line {
    position: absolute;
    left: 64px;
    font-size: 24px;
    letter-spacing: 1.4px;
    line-height: 30px;
    white-space: nowrap;
  }
  .intro { top: 209px; }
  .intro .highlight { background: var(--highlight); padding: 0 2px; }
  .offer-lead { top: 253px; left: 66px; }
  .offer-box {
    position: absolute;
    left: 65px;
    top: 311px;
    width: 569px;
    height: 181px;
    border: 5px solid var(--alert-red);
  }
  .offer-list {
    list-style: none;
    position: absolute;
    left: 20px;
    top: 11px;
  }
  .offer-list li {
    font-size: 24px;
    letter-spacing: 1.4px;
    line-height: 42px;
    white-space: nowrap;
  }
  .closing-1 { top: 520px; }
  .closing-2 { top: 563px; }
  .closing-3 { top: 610px; }
  .signature {
    position: absolute;
    left: 66px;
    top: 664px;
    width: 130px;
    height: 38px;
    background: var(--signature-tone);
    border-radius: 4px;
  }
  .contact {
    position: absolute;
    left: 66px;
    top: 719px;
    font-size: 17px;
    letter-spacing: 1.1px;
    line-height: 27px;
  }
  .contact .phone {
    font-size: 24px;
    font-weight: 700;
    letter-spacing: 1.6px;
    line-height: 34px;
    margin-top: 3px;
    margin-left: -3px;
  }
  .urgent-notice {
    position: absolute;
    left: 612px;
    top: 694px;
    width: 535px;
    height: 92px;
    background: var(--alert-red);
    color: var(--paper);
    font-size: 45px;
    font-weight: 700;
    letter-spacing: 3px;
    display: flex;
    align-items: center;
    justify-content: center;
  }
</style>
</head>
<body>
  <main class="postcard">
    <div class="brand-name">Harborline Asset Partners</div>

    <p class="copy-line intro">My name is Marcus. <span class="highlight">I am interested in buying your house!</span></p>
    <p class="copy-line offer-lead">We offer...</p>

    <section class="offer-box">
      <ul class="offer-list">
        <li>- CASH for your house ‘‘AS-IS’’</li>
        <li>- No inspactions or contingencies</li>
        <li>- Fast and lexible closing</li>
        <li>- No need to fix or clean out your home</li>
      </ul>
    </section>

    <p class="copy-line closing-1">There are never any obligations.</p>
    <p class="copy-line closing-2">If you’re interested, please contact us.</p>
    <p class="copy-line closing-3">We look forward to hearing from you!</p>

    <div class="signature" role="img" aria-label="Handwritten signature of Marcus"></div>

    <address class="contact" style="font-style: normal;">
      <div>Harborline Asset Partners, LLC</div>
      <div>www.harborlineassetpartners.com</div>
      <div>587 W Tessaly Ave, Suite 319, Baltimore, MD 21209</div>
      <div class="phone">(555) 274-1916</div>
    </address>

    <div class="urgent-notice">URGENT NOTICE</div>
  </main>
</body>
</html>
```